Where the Lantern Fades: A Sacred Wandering

This is a memoir about my breakdown/breakthrough followed by a spiritual awakening in 2012, I found my guru Harsh Omveli Dev, Mother Ayahuasca, and my spiritual mother, Ishu. By 2013, I was headed for a spiritual adventure through India, Southeast India, and Nepal which lasted 14 months. I lived in ashrams, meditated and prayed in temples,, traveled by train and bus, met many enlightened beings and interesting people. During Vipassana, I discovered my true essence- the light of my soul. It is a book of travel, romance, and spiritual growth. My idea is a road lined with temples, etc. I am walking down the road and see myself at the end of the road, facing out, with a bright star in my heart center. I see the colors in muted yellows and other earth-tone hues. Marigolds are used everywhere in the temples to adorn statues and doorways and this speaks to me. The title of the book is about finding out who I am beyond my stories and it is also about how our story will reveal to us who we really are.

Target Market(s)

Spiritual seekers, adventurers, travelers

Industry/Entity Type

Spiritual

Font styles to use
Serif
Sans Serif
Other font styles liked:
• I’m open. I like simplicity

Colors
FFC000
F8CF3A
FAE287
FDF2CF
FEFAEE

Requirements
Must have
• My name: Carla Serena Tovi, Earth tones, pastels, me or a likeness of me, room for ISBN on back cover
Nice to have
• In the photo uploads I drew an idea of what I would like, there is also the idea in the book
Should not have
• I am not a fan of bright colors and that's all I can select here. I like neutral colors, like browns, slate, creams, and whites. This reflects the dusty roads I took throughout my journey.

```html
<!DOCTYPE html>
<html lang="en">
<head>
<meta charset="utf-8">
<title>Where the Lantern Fades – Book Cover</title>
<link href="https://fonts.googleapis.com/css2?family=Della+Respira&family=Cinzel:wght@400;500&display=swap" rel="stylesheet">
<style>
  :root {
    --backdrop: #5f5f5f;
    --paper: #fcf5e8;
    --title: #b0657b;
    --band: #b0607a;
    --band-text: #fbf1ec;
    --ink: #3a3230;
    --frame: #ddd1bf;
  }
  * { margin: 0; padding: 0; box-sizing: border-box; }
  html, body {
    width: 1200px; height: 1200px; overflow: hidden;
    background: var(--backdrop);
  }
  .cover {
    position: absolute; left: 240px; top: 60px;
    width: 720px; height: 1080px;
    background: var(--paper);
    overflow: hidden;
  }
  .snapshot {
    position: absolute;
    background: var(--frame);
    padding: 9px;
    box-shadow: 0 2px 5px rgba(60, 40, 20, .25);
  }
  .snapshot .fill { width: 100%; height: 100%; }
  .title {
    position: absolute; left: 0; right: 0; top: 352px;
    text-align: center;
    font-family: "Della Respira", serif;
    font-weight: 400;
    font-size: 114px;
    line-height: 110px;
    color: var(--title);
    letter-spacing: -1px;
    z-index: 2;
  }
  .subtitle {
    position: absolute; left: 0; right: 0; top: 696px;
    text-align: center;
    font-family: "Cinzel", serif;
    font-size: 22px;
    letter-spacing: 2px;
    color: var(--ink);
    z-index: 2;
  }
  .author-band {
    position: absolute; left: 0; right: 0; bottom: 0;
    height: 50px;
    background: var(--band);
    display: flex; align-items: center; justify-content: center;
    font-family: "Cinzel", serif;
    font-size: 31px;
    letter-spacing: 3px;
    color: var(--band-text);
    z-index: 3;
  }
</style>
</head>
<body>
  <main class="cover">
    <!-- top collage -->
    <div class="snapshot" style="left:0;top:-10px;width:167px;height:75px;transform:rotate(-2deg)"><div class="fill" role="img" aria-label="Photo of a carved temple detail" style="background:#c9b9a0"></div></div>
    <div class="snapshot" style="left:80px;top:-10px;width:163px;height:167px;transform:rotate(3deg)"><div class="fill" role="img" aria-label="Photo of a painted deity artwork" style="background:linear-gradient(160deg,#d07a44,#b45a33)"></div></div>
    <div class="snapshot" style="left:2px;top:82px;width:158px;height:192px;transform:rotate(-4deg)"><div class="fill" role="img" aria-label="Photo of a golden statue" style="background:linear-gradient(180deg,#9aa3a8,#7c6a48)"></div></div>
    <div class="snapshot" style="left:60px;top:140px;width:175px;height:192px;transform:rotate(5deg)"><div class="fill" role="img" aria-label="Photo of a white and red temple tower" style="background:linear-gradient(180deg,#e6e8e4,#b98f6e)"></div></div>
    <div class="snapshot" style="left:210px;top:15px;width:167px;height:217px;transform:rotate(-3deg)"><div class="fill" role="img" aria-label="Photo of the author standing above a mountain valley" style="background:linear-gradient(180deg,#b5c4cc,#5e6a5a)"></div></div>
    <div class="snapshot" style="left:335px;top:140px;width:167px;height:167px;transform:rotate(4deg)"><div class="fill" role="img" aria-label="Photo of a shrine adorned with marigolds" style="background:linear-gradient(180deg,#d9d2c8,#b8624a)"></div></div>
    <div class="snapshot" style="left:377px;top:-8px;width:183px;height:170px;transform:rotate(-2deg)"><div class="fill" role="img" aria-label="Photo of a palace standing in a lake" style="background:linear-gradient(180deg,#c7cfd2,#8c8f86)"></div></div>
    <div class="snapshot" style="left:535px;top:-10px;width:133px;height:100px;transform:rotate(6deg)"><div class="fill" role="img" aria-label="Portrait photo of the author" style="background:#c9c4bd"></div></div>
    <div class="snapshot" style="left:560px;top:40px;width:170px;height:175px;transform:rotate(-3deg)"><div class="fill" role="img" aria-label="Photo of the author beneath a stone archway" style="background:linear-gradient(180deg,#b3a389,#6e4a3c)"></div></div>

    <h1 class="title">Where the<br>Lantern<br>Fades</h1>
    <p class="subtitle">A SACRED WANDERING</p>

    <!-- bottom collage -->
    <div class="snapshot" style="left:-6px;top:850px;width:174px;height:200px;transform:rotate(-3deg)"><div class="fill" role="img" aria-label="Photo of a pagoda temple square" style="background:linear-gradient(180deg,#c4d3dd,#8d7660)"></div></div>
    <div class="snapshot" style="left:152px;top:870px;width:108px;height:180px;transform:rotate(2deg)"><div class="fill" role="img" aria-label="Photo of the author in a shawl on a garden path" style="background:linear-gradient(180deg,#8c9a7c,#6e5a5a)"></div></div>
    <div class="snapshot" style="left:235px;top:785px;width:167px;height:175px;transform:rotate(5deg)"><div class="fill" role="img" aria-label="Photo of a sandstone fort" style="background:linear-gradient(180deg,#bfcbd6,#a9845e)"></div></div>
    <div class="snapshot" style="left:377px;top:860px;width:125px;height:190px;transform:rotate(-2deg)"><div class="fill" role="img" aria-label="Photo of a busy temple street" style="background:linear-gradient(180deg,#c5c9c6,#8a7a6a)"></div></div>
    <div class="snapshot" style="left:477px;top:912px;width:133px;height:130px;transform:rotate(3deg)"><div class="fill" role="img" aria-label="Photo of the author beside a colourful mural" style="background:linear-gradient(180deg,#8fb3c6,#c4a489)"></div></div>
    <div class="snapshot" style="left:502px;top:770px;width:167px;height:192px;transform:rotate(-5deg)"><div class="fill" role="img" aria-label="Smiling photo of the author before a pagoda" style="background:linear-gradient(180deg,#c9b6a0,#a0654e)"></div></div>
    <div class="snapshot" style="left:643px;top:825px;width:85px;height:140px;transform:rotate(4deg)"><div class="fill" role="img" aria-label="Photo of prayer flags over trees" style="background:linear-gradient(180deg,#a8b6c0,#6f7e5f)"></div></div>

    <footer class="author-band">CARLA SERENA TOVI</footer>
  </main>
</body>
</html>
```